bRu Design Group - architect web site

need a web site to permit potential clients to view our portfolio of work.

Will need lots of photos included.

Industry/Entity Type

Architect

Coding

Coded - Design and coding required

Number of Pages Required

5+ page

Font styles to use
Sans Serif

Requirements
Must have
• photos should be organized by project - perhaps a summary of photos and then click to enlarge? should be simple to operate. should be able to separate interior design from architecture.
• needs to be easy to add more photos in the future.

```html
<!DOCTYPE html>
<html lang="en">
<head>
<meta charset="utf-8">
<title>bRu Design Group</title>
<link href="https://fonts.googleapis.com/css2?family=Arimo:wght@400;700&display=swap" rel="stylesheet">
<style>
:root{
  --header:#8b8990;
  --band:#8a8891;
  --band-light:#a3a1a8;
  --news:#77757d;
  --accent:#9fc4ca;
  --accent-dark:#8fb6bc;
  --ink:#222;
  --muted:#555;
  --white:#fff;
  --footer:#2c2c2e;
}
*{margin:0;padding:0;box-sizing:border-box}
html,body{width:767px;height:1200px;overflow:hidden;background:var(--white)}
body{position:relative;font-family:"Arimo",Arial,sans-serif;color:var(--ink)}
.abs{position:absolute}

.site-header{left:0;top:0;width:767px;height:78px;background:var(--header)}
.brand{left:48px;top:18px;display:flex;align-items:center;gap:8px;color:var(--white);font-size:20px;font-weight:700;letter-spacing:.5px}
.brand-mark{width:14px;height:14px;background:var(--accent)}
.call{right:47px;top:20px;color:var(--white);font-size:8px;display:flex;align-items:center;gap:5px}
.call strong{font-size:12px;font-weight:400}
.nav{right:47px;top:50px;display:flex;gap:0;font-size:9.5px}
.nav a{color:var(--white);text-decoration:none;padding:5px 11px;height:19px;line-height:10px;display:block}
.nav a.active{background:var(--accent);padding:5px 16px;margin-right:8px}

.hero{left:0;top:78px;width:767px;height:344px;background:linear-gradient(180deg,#d8e6f2 0%,#c9d5e0 45%,#7d8ba3 75%,#9a7f6a 100%)}
.slide-btn{top:243px;width:29px;height:29px;background:rgba(90,90,95,.75);display:flex;align-items:center;justify-content:center}
.slide-btn.prev{left:0}.slide-btn.next{right:0}

.feature{top:466px;width:210px;height:120px}
.feature .icon{left:0;top:0;width:71px;height:71px;border-radius:50%;background:var(--accent);display:flex;align-items:center;justify-content:center}
.feature h3{left:83px;top:0;font-size:12.5px;font-weight:400;letter-spacing:.3px}
.feature p{left:83px;top:22px;width:124px;font-size:8px;line-height:14px;color:var(--muted);text-align:justify}
.btn{background:var(--accent);color:var(--white);font-size:8px;text-align:center;line-height:20px;height:20px}
.feature .btn{left:83px;top:87px;width:72px}

.welcome{left:0;top:609px;width:767px;height:234px;background:radial-gradient(ellipse at 40% 40%,var(--band-light) 0%,var(--band) 70%)}
.welcome h2{left:47px;top:33px;color:var(--white);font-size:18px;font-weight:400;letter-spacing:.3px}
.welcome .lead{left:47px;top:70px;width:440px;color:var(--white);font-size:7.5px;line-height:16px;text-align:justify}
.welcome .more{left:47px;top:177px;width:81px;height:23px;line-height:23px;background:#716f77;color:var(--white);font-size:8px;text-align:center}
.news-title{left:511px;top:34px;color:var(--white);font-size:14px}
.news-arrow{left:700px;top:33px;width:19px;height:18px;border:1px solid #a9a7ae}
.news-item{left:511px;width:209px;height:63px;background:var(--news);color:var(--white)}
.news-item .day{left:14px;top:10px;font-size:17px;font-weight:700}
.news-item .date{left:11px;top:35px;font-size:7.5px}
.news-item p{left:57px;top:10px;width:141px;font-size:7.5px;line-height:16px;text-align:justify}

.portfolio-title{left:47px;top:875px;font-size:18px;letter-spacing:.3px}
.pf-arrow{top:879px;width:19px;height:18px;border:1px solid #555;display:flex;align-items:center;justify-content:center}
.pf-arrow.next{border-color:#ccc}
.thumb{width:155px;height:92px}

.site-footer{left:0;top:1148px;width:767px;height:52px;background:var(--footer)}
.site-footer p{left:48px;top:20px;color:#ddd;font-size:7.5px}
.social{right:47px;top:15px;display:flex;gap:3px}
.social span{width:18px;height:18px;border-radius:50%;background:var(--white)}
</style>
</head>
<body>

<header class="site-header abs">
  <div class="brand abs"><span class="brand-mark"></span>bRu Design Group</div>
  <div class="call abs">
    <svg width="10" height="8" viewBox="0 0 10 8"><path d="M1 3 Q5 0 9 3 L8 4 L7 3 L3 3 L2 4Z M2 4 H8 V8 H2Z" fill="#fff"/></svg>
    Call Now: <strong>+33 71 40 5522</strong>
  </div>
  <nav class="nav abs">
    <a class="active" href="#">Home</a>
    <a href="#">About Us</a>
    <a href="#">Services</a>
    <a href="#">Testimonial</a>
    <a href="#">Showcase</a>
    <a href="#">Contact Us</a>
  </nav>
</header>

<section class="hero abs" role="img" aria-label="Four builders in hard hats reviewing plans at a construction site"></section>
<div class="slide-btn prev abs"><svg width="10" height="14" viewBox="0 0 10 14"><path d="M8 1 L2 7 L8 13" stroke="#fff" stroke-width="2" fill="none"/></svg></div>
<div class="slide-btn next abs"><svg width="10" height="14" viewBox="0 0 10 14"><path d="M2 1 L8 7 L2 13" stroke="#fff" stroke-width="2" fill="none"/></svg></div>

<div class="feature abs" style="left:48px">
  <div class="icon abs"><svg width="28" height="22" viewBox="0 0 28 22"><path d="M3 11 L11 19 L25 3" stroke="#fff" stroke-width="5" fill="none"/></svg></div>
  <h3 class="abs">LACINIA EST</h3>
  <p class="abs">Lorem ipsum dolor sit amet, consectetur adipiscing elit, sed do eiusmod tempor incididunt ut labore et dolor aliqua.</p>
  <div class="btn abs">Read More</div>
</div>
<div class="feature abs" style="left:281px">
  <div class="icon abs"><svg width="28" height="28" viewBox="0 0 28 28"><g fill="#fff"><circle cx="14" cy="14" r="9"/><rect x="11" y="1" width="6" height="26"/><rect x="1" y="11" width="26" height="6"/><rect x="11" y="1" width="6" height="26" transform="rotate(45 14 14)"/><rect x="11" y="1" width="6" height="26" transform="rotate(-45 14 14)"/></g><circle cx="14" cy="14" r="4" fill="#9fc4ca"/></svg></div>
  <h3 class="abs">VELIT FUSCE</h3>
  <p class="abs">Lorem ipsum dolor sit amet, consectetur adipiscing elit, sed do eiusmod tempor incididunt ut labore et dolor aliqua.</p>
  <div class="btn abs">Read More</div>
</div>
<div class="feature abs" style="left:512px;top:468px">
  <div class="icon abs"><svg width="28" height="28" viewBox="0 0 28 28"><path d="M19 3 L25 9 L10 24 L3 25 L4 18Z" fill="#fff"/><path d="M16 6 L22 12" stroke="#9fc4ca" stroke-width="1.5"/></svg></div>
  <h3 class="abs">DOLOR SIT</h3>
  <p class="abs">Lorem ipsum dolor sit amet, consectetur adipiscing elit, sed do eiusmod tempor incididunt ut labore et dolor aliqua.</p>
  <div class="btn abs">Read More</div>
</div>

<section class="welcome abs">
  <h2 class="abs">Welcome to Our Site..</h2>
  <p class="lead abs">Sed ut perspiciatis unde omnis iste natus error sit voluptatem accusantium doloremque laudantium, totam rem aperiam, eaque ipsa quae ab illo inventore veritatis et quasi architecto beatae vitae dicta sunt explicabo. Nemo enim ipsam voluptatem quia voluptas sit aspernatur aut odit aut fugit, sed quia consequuntur magni dolores eos qui ratione voluptatem sequi nesciunt. Neque porro quisquam est, qui dolorem ipsum quia dolor sit amet, consectetur, adipisci velit, sed quia non numquam eius modi tempora incidunt ut labore et dolore magnam aliquam quaerat voluptatem. Ut enim ad minima veniam, quis nostrum exercitationem ullam corporis suscipit laboriosam,</p>
  <div class="more abs">Read More</div>

  <h3 class="news-title abs">News &amp; Update</h3>
  <div class="news-arrow abs"></div>
  <article class="news-item abs" style="top:61px">
    <div class="day abs">02</div><div class="date abs">May 15</div>
    <p class="abs">Neque porro quisquam est, qui dolorem ipsum quia dolor sit amet, idunt ut labore et dolore</p>
  </article>
  <article class="news-item abs" style="top:135px">
    <div class="day abs">04</div><div class="date abs">May 15</div>
    <p class="abs">Neque porro quisquam est, qui dolorem ipsum quia dolor sit amet, idunt ut labore et dolore</p>
  </article>
</section>

<h2 class="portfolio-title abs">Our Portfolio</h2>
<div class="pf-arrow abs" style="left:677px"><svg width="9" height="7" viewBox="0 0 9 7"><path d="M8 3.5 H1 M3.5 1 L1 3.5 L3.5 6" stroke="#444" fill="none"/></svg></div>
<div class="pf-arrow next abs" style="left:701px"><svg width="9" height="7" viewBox="0 0 9 7"><path d="M1 3.5 H8 M5.5 1 L8 3.5 L5.5 6" stroke="#bbb" fill="none"/></svg></div>

<div class="thumb abs" style="left:47px;top:910px;background:linear-gradient(#6d6a6a,#cfcfcf)" role="img" aria-label="White architectural city model with crane"></div>
<div class="thumb abs" style="left:220px;top:910px;background:linear-gradient(#a9c8e6,#9a7b5e)" role="img" aria-label="Concrete building frame under construction"></div>
<div class="thumb abs" style="left:393px;top:910px;background:linear-gradient(135deg,#c8452e,#2c5fb0 55%,#7db04a)" role="img" aria-label="Colourful modern facade against blue sky"></div>
<div class="thumb abs" style="left:565px;top:910px;background:linear-gradient(135deg,#e9c77a,#3d6fa8 60%,#203d6c)" role="img" aria-label="Glass skyscrapers seen from below"></div>
<div class="thumb abs" style="left:47px;top:1020px;background:linear-gradient(#6b74b0,#c89b5a 70%,#3a3030)" role="img" aria-label="Modern office building lit at dusk"></div>
<div class="thumb abs" style="left:220px;top:1020px;background:linear-gradient(#cfe0ee,#8fb3d3 60%,#e2b53a)" role="img" aria-label="Laptop, hard hat and plans with cranes behind"></div>
<div class="thumb abs" style="left:393px;top:1020px;background:linear-gradient(#5f94c6,#d6c9a8)" role="img" aria-label="Tower crane over a construction site"></div>
<div class="thumb abs" style="left:565px;top:1020px;background:linear-gradient(90deg,#3c3c3c,#a8b8c6)" role="img" aria-label="High-rise under construction with cranes"></div>

<footer class="site-footer abs">
  <p class="abs">Copyright ©2015, Yoursite. All Right Reserved.</p>
  <div class="social abs"><span></span><span></span><span></span><span></span><span></span></div>
</footer>

</body>
</html>
```